Lmworks Business Card Design

I need a business card design for a new Business, that is focused on Custom Made Designer Furniture. that is aimed at the mid to high end markets. I would like a card that would in some way portray what I do for my clients in the way we are able to make any idea a reality and also work within a set budget to meet their requirements.
I like quite contemporary colours and styling and I want the final design to communicate a Contemporary and Professional image.

Target Market(s)

mid to high end market

Industry/Entity Type

Business

Contact Information for Business Card

Lmworks
Gareth Lindqvist
18 Wendover Ave, Auckland, New Zealand 0627.

Requirements
Nice to have
• I would also like to utilize the spot gloss or raised print on my cards

```html
<!DOCTYPE html>
<html lang="en">
<head>
<meta charset="utf-8">
<title>Lmworks Business Card</title>
<link rel="stylesheet" href="https://fonts.googleapis.com/css2?family=Poiret+One&display=swap">
<style>
  :root {
    --card-yellow: #f5d90a;
    --band-white: #ffffff;
    --ink: #111111;
  }
  * { margin: 0; padding: 0; box-sizing: border-box; }
  html, body {
    width: 1200px;
    height: 741px;
    overflow: hidden;
    background: var(--card-yellow);
  }
  .card {
    position: relative;
    width: 1200px;
    height: 741px;
    background: var(--card-yellow);
    color: var(--ink);
    font-family: "Poiret One", sans-serif;
  }
  .brand {
    position: absolute;
    left: 0;
    right: 0;
    top: 170px;
    display: flex;
    justify-content: center;
    align-items: center;
    gap: 22px;
  }
  .brand-mark {
    width: 26px;
    height: 26px;
    border-radius: 50%;
    background: var(--ink);
  }
  .brand-name {
    font-size: 96px;
    line-height: 1;
    letter-spacing: 2px;
    color: var(--ink);
  }
  .person {
    position: absolute;
    left: 0;
    right: 0;
    top: 366px;
    text-align: center;
  }
  .person-name {
    font-size: 56px;
    line-height: 1;
    letter-spacing: 1px;
  }
  .person-role {
    font-size: 32px;
    line-height: 1;
    margin-top: 2px;
    letter-spacing: 1px;
  }
  .address-band {
    position: absolute;
    left: 2px;
    right: 2px;
    top: 550px;
    height: 96px;
    background: var(--band-white);
    display: flex;
    align-items: center;
    justify-content: center;
  }
  .address {
    font-size: 30px;
    letter-spacing: 1px;
    font-style: normal;
  }
</style>
</head>
<body>
  <main class="card">
    <div class="brand">
      <span class="brand-mark" aria-hidden="true"></span>
      <span class="brand-name">Lmworks</span>
    </div>
    <div class="person">
      <h1 class="person-name">Gareth Lindqvist</h1>
      <p class="person-role">manager</p>
    </div>
    <div class="address-band">
      <address class="address">18 Wendover Ave, Auckland, New Zealand 0627</address>
    </div>
  </main>
</body>
</html>
```